Tech business card design

We need an amazing business card design for our new business 'Pexla' a marketing tech startup based in Sydney, Australia. We provide an online marketplace for businesses to search and buy advertising media, connect with service providers and learn more about marketing. We wish to communicate 'cool tech', reliability and professionalism and design based around our logo.

Target Market(s)

Business Owners

Contact Information for Business Card

Name
Position
Email Address
Website
Phone Number

Font styles to use
Other font styles liked:
• Avenir & Avenir Next

Colors

Designer to choose colors to be used in the design.

```html
<!DOCTYPE html>
<html lang="en">
<head>
<meta charset="UTF-8">
<title>Pexla Business Card</title>
<link rel="stylesheet" href="https://fonts.googleapis.com/css2?family=Nunito+Sans:wght@400;700;900&display=swap">
<style>
  :root {
    --navy: #161b4a;
    --white: #ffffff;
    --backdrop: #e6e7ec;
    --faint-mark: #6d6f93;
    --divider: #4a4f7a;
  }
  html, body {
    margin: 0;
    padding: 0;
    width: 1200px;
    height: 900px;
    overflow: hidden;
    background: var(--backdrop);
    font-family: "Nunito Sans", sans-serif;
  }
  .canvas {
    position: relative;
    width: 1200px;
    height: 900px;
  }
  .card {
    position: absolute;
    left: 300px;
    width: 600px;
    height: 343px;
    border-radius: 22px;
    overflow: hidden;
    box-shadow: 0 8px 24px rgba(0, 0, 0, 0.18);
  }
  .card-front {
    top: 80px;
    background: var(--white);
  }
  .card-back {
    top: 477px;
    background: var(--navy);
  }
  .front-wordmark {
    position: absolute;
    right: 44px;
    top: 6px;
    margin: 0;
    font-size: 104px;
    font-weight: 900;
    letter-spacing: -3px;
    color: var(--navy);
    line-height: 1;
  }
  .holder {
    position: absolute;
    left: 44px;
    top: 132px;
    color: var(--navy);
  }
  .holder-name {
    margin: 0;
    font-size: 17px;
    font-weight: 900;
    letter-spacing: 0.5px;
  }
  .holder-position {
    margin: 0 0 0 8px;
    font-size: 13px;
    font-weight: 700;
  }
  .info-band {
    position: absolute;
    left: 0;
    right: 0;
    top: 124px;
    height: 176px;
    background: var(--navy);
    clip-path: polygon(0 52%, 52% 52%, 52% 0, 100% 0, 100% 100%, 0 100%);
  }
  .address {
    position: absolute;
    left: 44px;
    top: 232px;
    color: var(--white);
    font-size: 15px;
    line-height: 1.25;
    margin: 0;
  }
  .band-divider {
    position: absolute;
    left: 326px;
    top: 198px;
    width: 1px;
    height: 74px;
    background: var(--divider);
  }
  .contact-list {
    position: absolute;
    left: 356px;
    top: 144px;
    margin: 0;
    padding: 0;
    list-style: none;
    color: var(--white);
    font-size: 15px;
    line-height: 1.35;
  }
  .contact-list li {
    display: flex;
    align-items: center;
    gap: 5px;
  }
  .contact-list svg {
    width: 12px;
    height: 12px;
    flex: none;
  }
  .back-wordmark {
    position: absolute;
    left: 0;
    right: 0;
    top: 82px;
    margin: 0;
    text-align: center;
    font-size: 160px;
    font-weight: 900;
    letter-spacing: -5px;
    line-height: 1;
    color: var(--faint-mark);
  }
</style>
</head>
<body>
<main class="canvas">
  <section class="card card-front" aria-label="Business card front">
    <div class="info-band"></div>
    <p class="front-wordmark">pexla</p>
    <div class="holder">
      <p class="holder-name">JOHN SMITH</p>
      <p class="holder-position">Position</p>
    </div>
    <p class="address">Street Name, City Name<br>&nbsp;Zipcode:012345</p>
    <div class="band-divider"></div>
    <ul class="contact-list">
      <li>
        <svg viewBox="0 0 24 24" aria-hidden="true"><path fill="#fff" d="M6.6 10.8a15.1 15.1 0 0 0 6.6 6.6l2.2-2.2a1 1 0 0 1 1-.25 11.4 11.4 0 0 0 3.6.57 1 1 0 0 1 1 1V20a1 1 0 0 1-1 1A17 17 0 0 1 3 4a1 1 0 0 1 1-1h3.5a1 1 0 0 1 1 1c0 1.25.2 2.45.57 3.57a1 1 0 0 1-.25 1z"/></svg>
        012-345-6789
      </li>
      <li>
        <svg viewBox="0 0 24 24" aria-hidden="true"><rect x="2" y="5" width="20" height="14" fill="#fff"/><path d="M2 5l10 8 10-8" fill="none" stroke="#161b4a" stroke-width="2"/></svg>
        info@pexla.com
      </li>
      <li style="padding-left:18px">
        <svg viewBox="0 0 24 24" aria-hidden="true"><g fill="none" stroke="#fff" stroke-width="2"><circle cx="12" cy="12" r="9"/><ellipse cx="12" cy="12" rx="4" ry="9"/><path d="M3 12h18M5 7h14M5 17h14"/></g></svg>
        www.pexla.com
      </li>
    </ul>
  </section>

  <section class="card card-back" aria-label="Business card back">
    <p class="back-wordmark">pexla</p>
  </section>
</main>
</body>
</html>
```